New Bicycle shop business card

Hi!
I'm looking for a business card for my new proffesional bike mechanics shop. This shop is only for fixing broken bikes and not selling bikes.
Peferbly a modern and sleek and modern design.
Colors: black, grey, red, white
Information:
Name: Rijwielwerkplaats Vanhoutte
Shop owner: Bart Vanhoutte & Marieke Segers
Website: www.rijwielwerkplaats-vanhoutte.be
Email: info@rijwielwerkplaats-vanhoutte.be
Phone number: +32471902368
Street adres: Kerkweg 46
9940 Bellebeke
Slogan/shop information: Herstellingen van alle merken.
Logo: see files.
Target Market(s)
People who seek a mechanic to fix or upgrade their bikes.
Contact Information for Business Card
Information:
Website: info@rijwielwerkplaats-vanhoutte.be
9940 Bellebeke
Logo: see files.

```html
<!DOCTYPE html>
<html lang="nl">
<head>
<meta charset="utf-8">
<title>Rijwielwerkplaats Vanhoutte – visitekaartje</title>
<link href="https://fonts.googleapis.com/css2?family=Michroma&family=Arimo:wght@400&display=swap" rel="stylesheet">
<style>
  :root {
    --red: #d22a3c;
    --black: #1a1a1a;
    --grey: #8f9296;
    --backdrop: #e4e4e4;
    --white: #ffffff;
    --card-white: #f7f7f7;
  }
  * { margin: 0; padding: 0; box-sizing: border-box; }
  html, body { width: 1200px; height: 852px; overflow: hidden; }
  body {
    background: var(--backdrop);
    position: relative;
    font-family: "Arimo", Arial, sans-serif;
  }
  .card {
    position: absolute;
    width: 540px;
    height: 309px;
    border-radius: 22px;
    overflow: hidden;
    box-shadow: 0 6px 18px rgba(0,0,0,0.18);
  }
  /* Front */
  .card-front {
    left: 70px; top: 150px;
    background: var(--red);
    display: flex; flex-direction: column; align-items: center;
  }
  .card-front .brand-mark {
    width: 18px; height: 18px; border-radius: 50%;
    background: var(--white);
    margin-top: 78px;
  }
  .card-front .wordmark {
    margin-top: 16px;
    font-family: "Michroma", sans-serif;
    color: var(--white);
    font-size: 20px;
    line-height: 1.35;
    text-align: center;
    letter-spacing: 1px;
  }
  .card-front .slogan {
    position: absolute; bottom: 40px; left: 0; right: 0;
    display: flex; align-items: center; justify-content: center; gap: 14px;
    color: var(--white); font-size: 14px;
  }
  .card-front .slogan::before,
  .card-front .slogan::after {
    content: ""; width: 40px; height: 1.5px; background: var(--white);
  }
  /* Back */
  .card-back {
    left: 590px; top: 400px;
    background: var(--card-white);
  }
  .card-back .accent-disc {
    position: absolute;
    right: -90px; top: -110px;
    width: 300px; height: 300px; border-radius: 50%;
    background: var(--red);
  }
  .card-back .wordmark {
    position: absolute; left: 34px; top: 38px;
    font-family: "Michroma", sans-serif;
    color: var(--black);
    font-size: 17px; line-height: 1.4;
    letter-spacing: 0.5px;
  }
  .card-back .person {
    position: absolute; left: 34px; top: 122px;
  }
  .person-name {
    font-family: "Michroma", sans-serif;
    color: var(--red); font-size: 16px; letter-spacing: 0.5px;
  }
  .person-role { font-size: 12px; color: var(--black); margin-top: 4px; }
  .contact {
    position: absolute; left: 34px; top: 188px;
    list-style: none; font-size: 13px; color: var(--black);
  }
  .contact li { display: flex; align-items: center; gap: 9px; height: 21px; }
  .contact svg { width: 12px; height: 12px; fill: var(--red); flex: none; }
  .contact .no-icon { padding-left: 21px; }
</style>
</head>
<body>
  <section class="card card-front" aria-label="Voorkant visitekaartje">
    <span class="brand-mark"></span>
    <p class="wordmark">RIJWIELWERKPLAATS<br>VANHOUTTE</p>
    <p class="slogan">Herstellingen van alle merken</p>
  </section>

  <section class="card card-back" aria-label="Achterkant visitekaartje">
    <span class="accent-disc"></span>
    <p class="wordmark">RIJWIELWERKPLAATS<br>VANHOUTTE</p>
    <div class="person">
      <p class="person-name">MARIEKE SEGERS</p>
      <p class="person-role">Owner</p>
    </div>
    <ul class="contact">
      <li>
        <svg viewBox="0 0 24 24" aria-hidden="true"><path d="M6.6 10.8a15.5 15.5 0 0 0 6.6 6.6l2.2-2.2a1 1 0 0 1 1-.25 11.4 11.4 0 0 0 3.6.57 1 1 0 0 1 1 1V20a1 1 0 0 1-1 1A17 17 0 0 1 3 4a1 1 0 0 1 1-1h3.5a1 1 0 0 1 1 1c0 1.25.2 2.45.57 3.6a1 1 0 0 1-.25 1z"/></svg>
        +32471902368
      </li>
      <li>
        <svg viewBox="0 0 24 24" aria-hidden="true"><path d="M12 2a10 10 0 1 0 0 20 10 10 0 0 0 0-20zm6.9 6h-2.9a15.6 15.6 0 0 0-1.4-3.6A8 8 0 0 1 18.9 8zM12 4c.8 1.2 1.5 2.5 1.9 4h-3.8c.4-1.5 1.1-2.8 1.9-4zM4.3 14a8 8 0 0 1 0-4h3.4a16 16 0 0 0 0 4zm.8 2h2.9c.3 1.3.8 2.5 1.4 3.6A8 8 0 0 1 5.1 16zM8 8H5.1a8 8 0 0 1 4.3-3.6C8.8 5.5 8.3 6.7 8 8zm4 12c-.8-1.2-1.5-2.5-1.9-4h3.8c-.4 1.5-1.1 2.8-1.9 4zm2.3-6H9.7a14.7 14.7 0 0 1 0-4h4.6a14.7 14.7 0 0 1 0 4zm.3 5.6c.6-1.1 1.1-2.3 1.4-3.6h2.9a8 8 0 0 1-4.3 3.6zm1.7-5.6a16 16 0 0 0 0-4h3.4a8 8 0 0 1 0 4z"/></svg>
        www.rijwielwerkplaats-vanhoutte.be
      </li>
      <li>
        <svg viewBox="0 0 24 24" aria-hidden="true"><path d="M2 5h20v14H2zm2 2v.5l8 5 8-5V7zm0 2.9V17h16V9.9l-8 5z"/></svg>
        info@rijwielwerkplaats-vanhoutte.be
      </li>
      <li class="no-icon">Kerkweg 46 9940 Bellebeke</li>
    </ul>
  </section>
</body>
</html>
```